Glow Club flyer design

I am launching an office Glow Club and would like a design that sits my branding and that is appealing to customers. I have a design (I need a new one) that has all the information.
My website is maplehavendentalcarekx.com
Brand color is green. The design can be any color

Target Market(s)

Ages 30+

Industry/Entity Type

Dental

Font styles to use
Serif

Requirements
Must have
• Appealing to patients

```html
<!DOCTYPE html>
<html lang="en">
<head>
<meta charset="utf-8">
<title>Maplehaven Dental Care – Glow Club Membership Flyer</title>
<link rel="stylesheet" href="https://fonts.googleapis.com/css2?family=Lora:wght@700&family=Marcellus&family=Poppins:wght@400;500;600;700;800&display=swap">
<style>
  :root{
    --backdrop:#213e37;
    --mint-edge:#8fdfd3;
    --mint-mid:#c6efe8;
    --mint-light:#dcf7f2;
    --teal:#17b6a5;
    --navy:#151b2a;
    --ink:#1a2133;
    --pink:#d8267f;
    --white:#ffffff;
  }
  *{box-sizing:border-box;margin:0;padding:0}
  html,body{width:1200px;height:1200px;overflow:hidden}
  body{background:var(--backdrop);font-family:"Poppins",sans-serif;color:var(--ink);position:relative}

  .flyer{position:absolute;left:245px;top:98px;width:710px;height:1004px;overflow:hidden;
    background:radial-gradient(ellipse 60% 45% at 50% 55%,var(--mint-light) 0%,var(--mint-mid) 60%,var(--mint-edge) 100%);
    box-shadow:0 10px 30px rgba(0,0,0,.35)}

  .floral{position:absolute;top:-40px;width:260px;height:340px;border-radius:50%;
    background:radial-gradient(closest-side,rgba(255,255,255,.35),rgba(255,255,255,0))}
  .floral--left{left:-80px}
  .floral--right{right:-80px}

  .brand{position:absolute;top:46px;left:0;width:100%;text-align:center}
  .brand__name{font-family:"Lora",serif;font-weight:700;font-size:44px;line-height:1;color:var(--ink);letter-spacing:-.5px}
  .brand__sub{display:flex;align-items:center;justify-content:center;gap:8px;margin-top:8px;
    font-weight:700;font-size:17px;letter-spacing:4px;color:var(--ink)}
  .brand__sub::before,.brand__sub::after{content:"";width:24px;height:2.5px;background:var(--ink)}

  .intro{position:absolute;top:152px;left:258px;width:193px;height:25px;border-radius:13px;background:var(--teal);
    color:var(--white);font-weight:700;font-size:15px;letter-spacing:4.5px;text-align:center;line-height:25px}

  .headline{font-family:"Marcellus",serif;color:var(--ink);font-weight:400}
  .headline__main{position:absolute;top:184px;left:0;width:100%;text-align:center;font-size:84px;line-height:84px;letter-spacing:1px}
  .headline__sub{position:absolute;top:262px;left:0;width:100%;text-align:center;font-size:40px;line-height:40px;letter-spacing:6px}

  .tag{position:absolute;top:310px;height:28px;border:1px solid var(--ink);border-radius:14px;color:var(--teal);
    font-weight:600;font-size:15px;text-align:center;line-height:26px}
  .tag--care{left:121px;width:237px}
  .tag--ins{left:368px;width:228px}

  .plan{position:absolute;width:306px;border:1px solid var(--teal);border-radius:22px;background:rgba(220,247,242,.55)}
  .plan--core{left:37px;top:360px;height:171px}
  .plan--bright{left:366px;top:360px;height:171px}
  .plan--perio{left:37px;top:552px;height:179px}
  .plan--refresh{left:366px;top:552px;height:179px}

  .plan__head{position:absolute;left:6px;right:5px;top:6px;height:50px;border-radius:25px;background:var(--teal);
    display:flex;align-items:center;justify-content:space-between}
  .plan__title{padding-left:15px;color:var(--white);font-weight:700;font-size:16.5px;line-height:17px;text-transform:uppercase}
  .plan__title--inset{padding-left:28px}
  .plan__price{height:37px;border-radius:19px;background:var(--navy);color:var(--white);display:flex;align-items:center;
    padding:0 14px 0 17px;font-weight:700;font-size:24px;gap:5px;flex:none}
  .plan__price small{font-weight:500;font-size:13px;color:var(--teal)}

  .badge-new{width:42px;height:42px;border-radius:50%;background:var(--pink);color:var(--white);margin-left:4px;
    display:flex;align-items:center;justify-content:center;font-weight:800;font-size:14px;transform:rotate(-12deg);flex:none}
  .plan--refresh .plan__title{padding-left:12px;flex:1}

  .plan__list{position:absolute;left:26px;top:68px;right:10px;list-style:none;font-size:13.5px;line-height:16px}
  .plan__list li{display:flex;align-items:flex-start;gap:6px;margin-bottom:4.5px}
  .plan__list li.plain{padding-left:15px}
  .tick{flex:none;width:9px;height:9px;margin-top:4px}
  .plus{display:inline-block;vertical-align:-1px;width:10px;height:10px;margin-left:3px}
  .plan--bright .plan__list{left:34px}
  .plan--refresh .plan__list{left:29px}
  .offer{font-family:"Marcellus",serif;font-size:17.5px;color:var(--teal);line-height:22px}

  .cta{position:absolute;left:0;top:759px;width:100%;height:46px;background:var(--teal);text-align:center;
    font-weight:800;font-size:24px;letter-spacing:1.6px;line-height:46px;color:var(--white)}
  .cta__phone{color:var(--navy)}

  .finance{position:absolute;left:0;top:805px;width:100%;height:199px;background:var(--navy);text-align:center;color:var(--white)}
  .finance__title{position:absolute;top:22px;width:100%;font-weight:600;font-size:14px;letter-spacing:2px}
  .finance__partners{position:absolute;top:48px;width:100%;display:flex;justify-content:center;gap:26px;align-items:center}
  .partner{font-weight:600;font-size:27px;display:flex;align-items:center;gap:7px}
  .partner--paywell{color:var(--teal)}
  .partner--plumline{color:#d9847c}
  .partner__dot{width:14px;height:14px;border-radius:50%;background:currentColor}
  .finance__plans{position:absolute;top:103px;width:100%;font-weight:600;font-size:13px;letter-spacing:2.4px;color:var(--teal)}
  .finance__fine{position:absolute;top:148px;width:100%;font-size:10px;letter-spacing:1.2px}
</style>
</head>
<body>
<main class="flyer">
  <div class="floral floral--left" role="img" aria-label="Soft white floral decoration"></div>
  <div class="floral floral--right" role="img" aria-label="Soft white floral decoration"></div>

  <header class="brand">
    <div class="brand__name">Maplehaven</div>
    <div class="brand__sub">DENTAL CARE</div>
  </header>

  <div class="intro">INTRODUCING</div>
  <h1 class="headline">
    <span class="headline__main">GLOW CLUB</span>
    <span class="headline__sub">MEMBERSHIP</span>
  </h1>

  <div class="tag tag--care">AFFORDABLE DENTAL CARE</div>
  <div class="tag tag--ins">NO INSURANCE REQUIRED</div>

  <svg width="0" height="0" style="position:absolute">
    <symbol id="tick" viewBox="0 0 10 10"><circle cx="5" cy="5" r="4.3" fill="none" stroke="#17b6a5" stroke-width="1"/><path d="M3 5.2l1.4 1.4L7 3.9" fill="none" stroke="#17b6a5" stroke-width="1"/></symbol>
    <symbol id="plus" viewBox="0 0 10 10"><circle cx="5" cy="5" r="5" fill="#17b6a5"/><path d="M5 2.5v5M2.5 5h5" stroke="#fff" stroke-width="1.4"/></symbol>
  </svg>

  <section class="plan plan--core">
    <div class="plan__head"><div class="plan__title">Daily Guard<br>Preventive</div><div class="plan__price">$39 <small>/MONTH</small></div></div>
    <ul class="plan__list">
      <li><svg class="tick"><use href="#tick"/></svg>Comprehensive Annual Exam</li>
      <li><svg class="tick"><use href="#tick"/></svg>2 Professional Cleanings per Year</li>
      <li><svg class="tick"><use href="#tick"/></svg>Routine Bitewing X-rays</li>
      <li><svg class="tick"><use href="#tick"/></svg>10% Savings on Treatment</li>
    </ul>
  </section>

  <section class="plan plan--bright">
    <div class="plan__head"><div class="plan__title plan__title--inset">Radiant<br>Cosmetic</div><div class="plan__price">$59 <small>/MONTH</small></div></div>
    <ul class="plan__list">
      <li><svg class="tick"><use href="#tick"/></svg>Annual In-Office Whitening<br>(Top &amp; Bottom)</li>
      <li><svg class="tick"><use href="#tick"/></svg>Custom Whitening Trays</li>
      <li><svg class="tick"><use href="#tick"/></svg>15% Savings on Elective Treatment</li>
    </ul>
  </section>

  <section class="plan plan--perio">
    <div class="plan__head"><div class="plan__title">Full Health<br>Periodontal</div><div class="plan__price">$89 <small>/MONTH</small></div></div>
    <ul class="plan__list">
      <li><svg class="tick"><use href="#tick"/></svg>3-4 Perio Maintenance Visits per Year</li>
      <li><svg class="tick"><use href="#tick"/></svg>1 Comprehensive Exam</li>
      <li><svg class="tick"><use href="#tick"/></svg>Diagnostic X-rays</li>
      <li><svg class="tick"><use href="#tick"/></svg>15% Savings on Restorative &amp;<br>Elective Care</li>
    </ul>
  </section>

  <section class="plan plan--refresh">
    <div class="plan__head"><div class="badge-new">NEW</div><div class="plan__title">Fresh Start<br>Package</div><div class="plan__price">$499</div></div>
    <ul class="plan__list">
      <li><svg class="tick"><use href="#tick"/></svg>&nbsp;Cleaning<svg class="plus"><use href="#plus"/></svg></li>
      <li class="plain">&nbsp;Comprehensive Exam<svg class="plus"><use href="#plus"/></svg></li>
      <li class="plain">&nbsp;Whitening</li>
      <li><svg class="tick" style="margin-top:7px"><use href="#tick"/></svg>&nbsp;<span class="offer">Limited Time Offer</span></li>
    </ul>
  </section>

  <div class="cta">JOIN GLOW CLUB TODAY! <span class="cta__phone">865-555-0142</span></div>

  <footer class="finance">
    <div class="finance__title">FLEXIBLE FINANCING FOR TREATMENT</div>
    <div class="finance__partners">
      <div class="partner partner--paywell"><span class="partner__dot"></span>PayWell</div>
      <div class="partner partner--plumline"><span class="partner__dot"></span>Plumline</div>
    </div>
    <div class="finance__plans">PAYMENT PLANS AVAILABLE</div>
    <div class="finance__fine">*$49 Lifetime Activation Fee (Non-Refundable)</div>
  </footer>
</main>
</body>
</html>
```